International oil and gas consultancy business needs a web design

Hello, I need a web design for a new oil and gas auditing consultancy business. My business undertakes contract audit assignments to review past costs of oil and gas operations (see attached Excel file for more details of the businesses services). I need the design to give the impression of a professional consultancy style of business, rather than a retail style of website. Note: this job is for LAYOUT DESIGN ONLY and not coding / development work.
The following are my key design principles:
1. BASIC DESIGN: I am after a simple and static web design. I don't want the pages busy or cluttered with too many images or detail.
2. HORIZONTAL TABS: I require a horizontal set of tabs towards the top of the screens (see Excel file) which remain in the same position on every page.
3. META TAG PLANNING: The design should allow for effective positioning of content so that key meta tag words can easily be built during the technical build stage.
4. NUMBER OF PAGES: The site will eventually have a maximum of 10 pages. Seven of the pages will reside under the tabs. Can you please present your opening submission for the first two page.
5. USE OF MY LOGO: The attached logo (JPEG file) should be used throughout the website. Please don't change the shape and colour.
6. COLOUR SCHEMES: Can you please consider any of the 3 colour schemes below:
A - dark red (to match the logo), light grey and perhaps another of your liking;
B - dark red (to match the logo), light cream and perhaps another of your liking;
C - dark red (to match the logo), white and perhaps another of your liking.
7. WORD CONTENT: I have attached an Excel file which shows the estimated word content for each page.
8. FUTURE USE OF DESIGN: I'm planning on building a Wordpress website. Can you please ensure the layout design supports this application.

Target Market(s)

oil and gas companies (small and large)

Industry/Entity Type

Oil And Gas

Font styles to use
Sans Serif

Requirements
Nice to have
• The KRL logo and business name should ideally be next to each other. Also, the logo and name should be part of the background graphics, not above it.

```html
<!DOCTYPE html>
<html lang="en">
<head>
<meta charset="utf-8">
<title>Kestrel Review Labs</title>
<link rel="stylesheet" href="https://fonts.googleapis.com/css2?family=Open+Sans:wght@400;600&display=swap">
<style>
  :root {
    --brand-red: #8e1b1f;
    --text-grey: #6e6e6e;
    --nav-grey: #666666;
    --light-panel: #f8f8fa;
    --footer-bg: #f2f2f2;
    --rule: #d6d6d6;
    --dot: #c4c4c6;
    --dot-active: #9a9a9c;
    --social: #3a86c8;
    --white: #ffffff;
  }
  * { box-sizing: border-box; margin: 0; padding: 0; }
  html, body { width: 1200px; height: 1127px; overflow: hidden; }
  body {
    background: var(--white);
    font-family: "Open Sans", sans-serif;
    color: var(--text-grey);
    position: relative;
  }
  .wrap { width: 1002px; margin-left: 99px; position: relative; }

  /* Header */
  .site-header { height: 129px; position: relative; }
  .brand {
    position: absolute; left: 0; top: 20px;
    color: var(--brand-red); font-weight: 600; text-decoration: none;
    display: flex; flex-direction: column;
  }
  .brand-mark { font-size: 50px; line-height: 54px; letter-spacing: 3px; }
  .brand-name { font-size: 11px; line-height: 16px; letter-spacing: 0.1px; }
  .main-nav {
    position: absolute; right: 0; top: 36px;
    display: flex; gap: 31px; list-style: none;
  }
  .main-nav a {
    font-size: 13.5px; color: var(--nav-grey); text-decoration: none;
  }
  .main-nav a.is-current { color: var(--brand-red); }

  /* Hero */
  .hero { height: 445px; display: flex; }
  .hero-photo {
    width: 710px; height: 445px;
    background: linear-gradient(120deg, #eef1f4 0%, #dfe4ea 45%, #f3f4f6 100%);
  }
  .hero-text {
    flex: 1; background: var(--light-panel);
    padding: 70px 28px 0 33px; position: relative;
  }
  .hero-title {
    color: var(--brand-red); font-weight: 400;
    font-size: 26px; line-height: 29px; margin-bottom: 22px;
  }
  .hero-copy { font-size: 13px; line-height: 23px; color: var(--text-grey); }
  .slider-dots {
    position: absolute; left: 103px; top: 382px;
    display: flex; gap: 11px; list-style: none;
  }
  .slider-dots li {
    width: 13px; height: 13px; border-radius: 50%; background: var(--dot);
  }
  .slider-dots li.is-active { background: var(--dot-active); }

  /* Services */
  .services-title {
    text-align: center; font-weight: 400; font-size: 20.5px;
    color: #7a7a7a; margin-top: 52px; letter-spacing: 0.1px;
  }
  .service-list {
    display: flex; gap: 16px; list-style: none; margin-top: 29px;
  }
  .service-card { width: 323px; text-align: center; }
  .service-photo { height: 184px; }
  .service-photo.joint { background: linear-gradient(135deg, #c9ccd4 0%, #b7a9c6 50%, #8f8c90 100%); }
  .service-photo.contract { background: linear-gradient(135deg, #f7f7f7 0%, #e6e7ea 60%, #d5d2cf 100%); }
  .service-photo.operations { background: linear-gradient(135deg, #c99a79 0%, #e2cf9a 45%, #3a2c29 100%); }
  .service-name {
    color: var(--brand-red); font-weight: 600; font-size: 20.5px;
    margin-top: 17px; letter-spacing: 0.2px;
  }

  /* Footer */
  .site-footer {
    position: absolute; left: 0; top: 961px; width: 1200px; height: 166px;
    background: var(--footer-bg);
  }
  .footer-nav {
    display: flex; justify-content: center; list-style: none;
    margin-top: 27px; font-size: 13.5px;
  }
  .footer-nav li + li::before { content: "/"; margin: 0 11px; color: #9a9a9a; }
  .footer-nav a { color: var(--nav-grey); text-decoration: none; }
  .footer-rule { border: 0; border-top: 1px solid var(--rule); margin-top: 24px; }
  .footer-bottom {
    display: flex; justify-content: space-between; align-items: center;
    margin-top: 26px;
  }
  .legal { display: flex; list-style: none; font-size: 13.5px; color: var(--nav-grey); }
  .legal li + li::before { content: "/"; margin: 0 11px; color: #9a9a9a; }
  .legal a { color: var(--nav-grey); text-decoration: none; }
  .social { display: flex; gap: 13px; list-style: none; margin-right: 1px; }
  .social li {
    width: 33px; height: 33px; border-radius: 50%; background: var(--social);
  }
</style>
</head>
<body>
  <div class="wrap">
    <header class="site-header">
      <a class="brand" href="#">
        <span class="brand-mark">KRL</span>
        <span class="brand-name">KESTREL REVIEW LABS</span>
      </a>
      <ul class="main-nav">
        <li><a class="is-current" href="#">HOME</a></li>
        <li><a href="#">ABOUT US</a></li>
        <li><a href="#">SERVICES</a></li>
        <li><a href="#">OUR PARTNERS</a></li>
        <li><a href="#">APPROACH</a></li>
        <li><a href="#">WHY CHOOSE US</a></li>
        <li><a href="#">CONTACT US</a></li>
      </ul>
    </header>

    <section class="hero">
      <div class="hero-photo" role="img" aria-label="Photo of a smiling auditor at a bright office desk with binders and a calculator"></div>
      <div class="hero-text">
        <h1 class="hero-title">KESTREL REVIEW<br>LABS</h1>
        <p class="hero-copy">is a Perth (Australia) based firm specialising in providing quality audit services for the oil and gas industry. Our skills and knowledge of oil and gas, along with a deep understanding of business commer-cial needs, ensures the high quality of our services.</p>
        <ul class="slider-dots">
          <li class="is-active"></li><li></li><li></li><li></li>
        </ul>
      </div>
    </section>

    <section class="services">
      <h2 class="services-title">KESTREL REVIEW LABS SPECIALISE IN THE FOLLOWING SERVICES :</h2>
      <ul class="service-list">
        <li class="service-card">
          <div class="service-photo joint" role="img" aria-label="Photo of business partners shaking hands at a meeting table"></div>
          <h3 class="service-name">JOINT VENTURE AUDITS</h3>
        </li>
        <li class="service-card">
          <div class="service-photo contract" role="img" aria-label="Photo of a consultant reviewing documents beside a laptop"></div>
          <h3 class="service-name">CONTRACT AUDITS</h3>
        </li>
        <li class="service-card">
          <div class="service-photo operations" role="img" aria-label="Photo of a tablet showing charts lying on printed reports"></div>
          <h3 class="service-name">OPERATIONS AUDITS</h3>
        </li>
      </ul>
    </section>
  </div>

  <footer class="site-footer">
    <ul class="footer-nav">
      <li><a href="#">HOME</a></li>
      <li><a href="#">ABOUT US</a></li>
      <li><a href="#">SERVICES</a></li>
      <li><a href="#">OUR PARTNERS</a></li>
      <li><a href="#">APPROACH</a></li>
      <li><a href="#">WHY CHOOSE US</a></li>
      <li><a href="#">CONTACT US</a></li>
    </ul>
    <div class="wrap">
      <hr class="footer-rule">
      <div class="footer-bottom">
        <ul class="legal">
          <li>Copyright c&nbsp; 2014 Kestrel Review Labs</li>
          <li><a href="#">Terms and Conditions</a></li>
          <li><a href="#">Privacy policy</a></li>
        </ul>
        <ul class="social">
          <li aria-label="Social network link"></li>
          <li aria-label="Social network link"></li>
          <li aria-label="Social network link"></li>
        </ul>
      </div>
    </div>
  </footer>
</body>
</html>
```